Telecommunications/Power civil contractor needs business card design

Were a new telecommunications/power underground civil contractor that is looking for a new business card design. Our company colours are silver or grey and orange. Feel free to use the white background logo or the black background logo.

Target Market(s)

Local contractors, utility companies, private sector mining/energy companies, developers.

Industry/Entity Type

Telecommunications

Contact Information for Business Card

Each card will need the following info:
Persons name:
Title:
E-mail:
Phone number:
Shop Address:
Mailing Address:

Requirements
Must have
• Each card will need the following info:
• Persons name:
• Title:
• E-mail:
• Phone number:
• Shop Address:
• Mailing Address:

```html
<!DOCTYPE html>
<html lang="en">
<head>
<meta charset="utf-8">
<title>Dunmore Contracting Inc — Business Card</title>
<link rel="stylesheet" href="https://fonts.googleapis.com/css2?family=Roboto:wght@300;400;700&display=swap">
<style>
  :root {
    --stage: #e6e4e1;
    --card-dark: #2b2b2b;
    --card-light: #ececec;
    --orange: #f05a22;
    --silver: #8a8a8a;
    --silver-light: #c9c9c9;
    --text-light: #d6d6d6;
    --white: #ffffff;
  }
  * { box-sizing: border-box; margin: 0; padding: 0; }
  html, body { width: 1200px; height: 864px; overflow: hidden; }
  body {
    background: var(--stage);
    font-family: "Roboto", Arial, sans-serif;
    position: relative;
  }
  .card {
    position: absolute;
    top: 277px;
    width: 540px;
    height: 309px;
    border-radius: 4px;
    overflow: hidden;
    box-shadow: 0 8px 24px rgba(0,0,0,0.22);
  }
  .card--back { left: 40px; background: var(--card-dark); }
  .card--front { left: 620px; background: var(--card-light); }

  .brand {
    position: absolute;
    display: flex;
    flex-direction: column;
    align-items: center;
    gap: 14px;
  }
  .brand__ring {
    width: 96px; height: 96px;
    border-radius: 50%;
    border: 6px solid var(--silver);
  }
  .brand__name {
    font-weight: 700;
    color: var(--orange);
    text-transform: uppercase;
    letter-spacing: 2px;
    text-align: center;
    line-height: 1.15;
  }
  .card--back .brand { left: 0; right: 0; top: 52px; }
  .card--back .brand__name { font-size: 30px; }
  .card--front .brand { left: 330px; right: 14px; top: 78px; gap: 12px; }
  .card--front .brand__ring { width: 70px; height: 70px; border-width: 5px; }
  .card--front .brand__name { font-size: 18px; letter-spacing: 1.5px; }

  .card__split { position: absolute; inset: 0; }

  .contact {
    position: absolute;
    left: 30px;
    top: 30px;
    color: var(--text-light);
  }
  .contact__name { font-size: 26px; font-weight: 300; color: var(--white); }
  .contact__title { font-size: 14px; font-weight: 300; color: var(--orange); margin-top: 2px; }
  .contact__address { font-size: 13px; font-weight: 300; line-height: 1.45; margin-top: 22px; }
  .contact__list { list-style: none; margin-top: 18px; font-size: 13px; font-weight: 300; }
  .contact__list li { display: flex; align-items: center; gap: 9px; height: 21px; }
  .contact__icon {
    width: 15px; height: 15px;
    border-radius: 3px;
    background: var(--silver-light);
    display: flex; align-items: center; justify-content: center;
  }
  .contact__icon svg { width: 11px; height: 11px; }
</style>
</head>
<body>

  <section class="card card--back" aria-label="Card back">
    <div class="brand">
      <div class="brand__ring"></div>
      <div class="brand__name">Dunmore<br>Contracting Inc</div>
    </div>
  </section>

  <section class="card card--front" aria-label="Card front">
    <svg class="card__split" viewBox="0 0 540 309" preserveAspectRatio="none">
      <path d="M0 0 H330 C300 110 300 200 330 309 H0 Z" fill="var(--card-dark)"/>
      <path d="M330 0 C300 110 300 200 330 309" fill="none" stroke="var(--silver-light)" stroke-width="5"/>
    </svg>

    <div class="contact">
      <p class="contact__name">Alex Morgan</p>
      <p class="contact__title">General Manager</p>
      <p class="contact__address">Street Address, Suite 00<br>Statename 00000</p>
      <ul class="contact__list">
        <li>
          <span class="contact__icon"><svg viewBox="0 0 12 12"><path d="M3 1 L5 3.5 L4 5 Q5 7 7 8 L8.5 7 L11 9 L9.5 11 Q4 10.5 1 3 Z" fill="#2b2b2b"/></svg></span>
          555 0142 2345
        </li>
        <li>
          <span class="contact__icon"><svg viewBox="0 0 12 12"><rect x="3.5" y="1" width="5" height="10" rx="1" fill="none" stroke="#2b2b2b" stroke-width="1.3"/></svg></span>
          555 0187 9876
        </li>
        <li>
          <span class="contact__icon"><svg viewBox="0 0 12 12"><rect x="1" y="2.5" width="10" height="7" fill="none" stroke="#2b2b2b" stroke-width="1.2"/><path d="M1 2.5 L6 6.5 L11 2.5" fill="none" stroke="#2b2b2b" stroke-width="1.2"/></svg></span>
          info@corelinetech.com
        </li>
        <li>
          <span class="contact__icon"><svg viewBox="0 0 12 12"><circle cx="6" cy="6" r="4.6" fill="none" stroke="#2b2b2b" stroke-width="1.2"/><path d="M1.4 6 H10.6 M6 1.4 Q3.5 6 6 10.6 Q8.5 6 6 1.4" fill="none" stroke="#2b2b2b" stroke-width="1"/></svg></span>
          www.corelinetech.com
        </li>
      </ul>
    </div>

    <div class="brand">
      <div class="brand__ring"></div>
      <div class="brand__name">Dunmore<br>Contracting Inc</div>
    </div>
  </section>

</body>
</html>
```